Maple Gable Business Card

Colors can be blue, grey and white as you see in the attached logo. Needs to have a spot for name, title, phone, email, address, and website. There also needs to be a spot for an agent's picture.

Contact Information for Business Card

See project description.

Colors

Designer to choose colors to be used in the design.

```html
<!DOCTYPE html>
<html lang="en">
<head>
<meta charset="UTF-8">
<title>Maple Gable Business Card</title>
<link href="https://fonts.googleapis.com/css2?family=Roboto:wght@400;500&family=Montserrat:wght@600&display=swap" rel="stylesheet">
<style>
  :root {
    --page: #e9eaec;
    --card-dark: #25272a;
    --brand-blue: #2a78c0;
    --text-light: #f1f1f1;
    --rule: #8a8d92;
    --white: #ffffff;
  }
  * { box-sizing: border-box; margin: 0; padding: 0; }
  html, body { width: 1200px; height: 1108px; overflow: hidden; }
  body {
    background: var(--page);
    font-family: "Roboto", Arial, sans-serif;
    position: relative;
  }
  .card {
    position: absolute;
    top: 204px;
    width: 420px;
    height: 700px;
    border-radius: 24px;
    overflow: hidden;
    background: var(--card-dark);
    box-shadow: 0 14px 30px rgba(0,0,0,0.25);
  }
  .card--front { left: 150px; }
  .card--back { left: 630px; }

  .agent-photo {
    position: absolute;
    left: 0; top: 0;
    width: 420px; height: 390px;
    background: radial-gradient(ellipse at 55% 55%, #4a4d52 0%, #2e3034 55%, var(--card-dark) 80%);
  }
  .agent-info {
    position: absolute;
    left: 0; right: 0; top: 368px;
    text-align: center;
    color: var(--text-light);
  }
  .agent-name {
    color: var(--brand-blue);
    font-weight: 500;
    font-size: 34px;
    line-height: 1.1;
  }
  .agent-title { font-size: 22px; margin-top: 2px; }
  .icon-rule {
    display: flex; align-items: center; justify-content: center;
    gap: 8px; margin: 12px 40px 10px;
  }
  .icon-rule .rule { flex: 1; height: 1px; background: var(--rule); }
  .contact-icon { width: 26px; height: 26px; }
  .contact-list { font-size: 22px; line-height: 1.3; }
  .contact-list .accent { color: var(--brand-blue); }
  .divider { height: 1px; background: var(--rule); margin: 14px 40px 12px; }
  .address { font-size: 22px; line-height: 1.3; }

  .house-art { position: absolute; inset: 0; }
  .brand-name {
    position: absolute;
    left: 0; right: 0; top: 540px;
    text-align: center;
    font-family: "Montserrat", Arial, sans-serif;
    font-weight: 600;
    font-size: 44px;
    color: var(--white);
    letter-spacing: 1px;
  }
</style>
</head>
<body>
  <section class="card card--front">
    <div class="agent-photo" role="img" aria-label="Portrait photo of the agent in a dark suit"></div>
    <div class="agent-info">
      <h1 class="agent-name">Daniel Hart</h1>
      <p class="agent-title">Manager</p>
      <div class="icon-rule">
        <span class="rule"></span>
        <svg class="contact-icon" viewBox="0 0 26 26" aria-label="phone">
          <circle cx="13" cy="13" r="13" fill="var(--brand-blue)"/>
          <path d="M8 8h4l1 3-2 1.5a8 8 0 0 0 3.5 3.5L16 14l3 1v4c-6 0-11-5-11-11z" fill="var(--card-dark)"/>
        </svg>
        <svg class="contact-icon" viewBox="0 0 26 26" aria-label="email">
          <circle cx="13" cy="13" r="13" fill="var(--brand-blue)"/>
          <rect x="6.5" y="8.5" width="13" height="9" fill="var(--card-dark)"/>
          <path d="M6.5 8.5l6.5 5 6.5-5" stroke="var(--brand-blue)" stroke-width="1.4" fill="none"/>
        </svg>
        <svg class="contact-icon" viewBox="0 0 26 26" aria-label="website">
          <circle cx="13" cy="13" r="13" fill="var(--brand-blue)"/>
          <circle cx="13" cy="13" r="6.5" fill="none" stroke="var(--card-dark)" stroke-width="1.6"/>
          <ellipse cx="13" cy="13" rx="2.8" ry="6.5" fill="none" stroke="var(--card-dark)" stroke-width="1.4"/>
          <path d="M6.5 13h13" stroke="var(--card-dark)" stroke-width="1.4"/>
        </svg>
        <span class="rule"></span>
      </div>
      <div class="contact-list">
        <p>123-456-2100</p>
        <p>youremail@maplegable.com</p>
        <p>www.<span class="accent">yourwebsite</span>.com</p>
      </div>
      <div class="divider"></div>
      <div class="address">
        <p>Your address, city</p>
        <p>state, ZIP 0000</p>
      </div>
    </div>
  </section>

  <section class="card card--back">
    <svg class="house-art" viewBox="0 0 420 700" aria-hidden="true">
      <polygon points="0,262 292,150 420,300 420,336 292,178 0,280" fill="var(--white)"/>
      <polygon points="0,272 292,178 420,336 420,700 0,700" fill="var(--brand-blue)"/>
    </svg>
    <p class="brand-name">Maple Gable</p>
  </section>
</body>
</html>
```